Etikett für einen Rosé Wein
Zielgruppe
Wir sind ein Weingut und benötigen ein neues Etikett für unseren Muskattrollinger Rosé. Unsere Kunden sind eher traditionelle Weinkäufer.
Aufgabenstellung
Format:
Höhe: 9 cm
Breite: 11 cm
Da es nur ein Vorderetikett gibt, müssen alle relevanten Angaben (Hersteller, Alkohol, Inhalt in L, Rebsorte, etc.) enthalten sein. (siehe Flaschenabbildung anbei)
WÜRTTEMBERG
2019er
Muskattrollinger Rosé
DEUTSCHER QUALITÄTSWEIN
11,0 % Vol.
0,75 l
Enthält Sulfite
A.P.Nr. 58127364
Abfüller
Straße / PLZ / Ort / Tel.
Der Flaschenverschluss ist schwarz d.h. das neue Etikettendesign sollte dazu passen.
Bisher ist der Hintergrund des Weinetiketts schwarz. Dies muss jedoch nicht so bleiben.
Im Anhang finden Sie außerdem ein Plakat. Ggf. können Sie für das Flaschendesign einige nostalgische Elemente davon übernehmen.

```html
<!DOCTYPE html>
<html lang="de">
<head>
<meta charset="utf-8">
<title>Muskattrollinger Rosé – Weinetikett</title>
<link rel="stylesheet" href="https://fonts.googleapis.com/css2?family=Grenze+Gotisch:wght@500;600&family=Caudex:wght@400;700&display=swap">
<style>
  :root {
    --page: #ffffff;
    --label-bg: #363636;
    --teal: #38828a;
    --teal-line: #3a8a92;
    --ink: #ffffff;
    --ink-soft: #e2e2e2;
    --sketch-light: #cfcfcf;
    --sketch-dark: #6a6a6a;
  }
  html, body {
    margin: 0;
    padding: 0;
    width: 728px;
    height: 1200px;
    overflow: hidden;
    background: var(--page);
  }
  .canvas {
    position: relative;
    width: 728px;
    height: 1200px;
  }
  .wine-label {
    position: absolute;
    left: 44px;
    top: 339px;
    width: 640px;
    height: 522px;
    display: block;
  }
  .label-bg { fill: var(--label-bg); }
  .frame-line { stroke: var(--teal-line); stroke-width: 4; fill: none; }
  .variety-band { fill: var(--teal); }
  .ornament { fill: var(--teal-line); opacity: 0.55; }
  .sketch { fill: url(#sketchTone); }
  .gothic {
    font-family: "Grenze Gotisch", serif;
    font-weight: 600;
    fill: var(--ink);
  }
  .serif {
    font-family: "Caudex", serif;
    fill: var(--ink);
  }
  .meta { font-size: 48px; }
  .quality-arc { font-size: 36px; font-weight: 700; letter-spacing: 1px; }
  .region { font-size: 40px; font-weight: 700; letter-spacing: 2px; }
  .variety { font-size: 124px; }
  .variety-style { font-size: 112px; fill: var(--ink-soft); }
  .small-info { font-size: 34px; font-weight: 700; letter-spacing: 1px; }
  .bottler { font-size: 44px; font-weight: 700; letter-spacing: 2px; word-spacing: 8px; }
</style>
</head>
<body>
<main class="canvas">
  <svg class="wine-label" viewBox="0 0 1088 888" xmlns="http://www.w3.org/2000/svg" aria-label="Weinetikett Muskattrollinger Rosé">
    <defs>
      <linearGradient id="sketchTone" x1="0" y1="0" x2="1" y2="1">
        <stop offset="0" stop-color="var(--sketch-light)" stop-opacity="0.85"/>
        <stop offset="1" stop-color="var(--sketch-dark)" stop-opacity="0.6"/>
      </linearGradient>
      <path id="qualityArc" d="M 280 212 Q 544 60 815 212"/>
    </defs>

    <rect class="label-bg" x="0" y="0" width="1088" height="888"/>

    <!-- frame -->
    <path class="frame-line" d="M43 35 H262 M827 35 H1045 M45 35 V357 M1043 35 V357 M45 578 V852 M1043 578 V852 M43 852 H262 M827 852 H1045"/>
    <rect class="ornament" role="img" aria-label="Verschnörkeltes Ornament oben" x="285" y="24" width="520" height="40" rx="20"/>
    <rect class="ornament" role="img" aria-label="Verschnörkeltes Ornament unten" x="285" y="825" width="520" height="40" rx="20"/>

    <!-- head -->
    <text class="gothic meta" x="66" y="108">11,0 % Vol.</text>
    <text class="gothic meta" x="66" y="158">0,75 l</text>
    <text class="gothic meta" x="1022" y="110" text-anchor="end">2019er</text>

    <text class="serif quality-arc"><textPath href="#qualityArc" startOffset="50%" text-anchor="middle">DEUTSCHER QUALITÄTSWEIN</textPath></text>

    <rect class="sketch" role="img" aria-label="Gezeichnete Weintraube mit Weinblatt" x="420" y="158" width="260" height="106" rx="40"/>

    <text class="serif region" x="544" y="318" text-anchor="middle">WÜRTTEMBERG</text>

    <!-- variety band -->
    <rect class="variety-band" x="43" y="357" width="1002" height="221"/>
    <text class="gothic variety" x="544" y="464" text-anchor="middle">Muskattrollinger</text>
    <text class="gothic variety-style" x="544" y="556" text-anchor="middle">Rosé</text>

    <!-- legal info -->
    <text class="serif small-info" x="63" y="660">Enthält Sulfite</text>
    <text class="serif small-info" x="1024" y="660" text-anchor="end">A.P. Nr.58127364</text>

    <rect class="sketch" role="img" aria-label="Gezeichnetes Weinblatt links" x="62" y="692" width="136" height="138" rx="34"/>
    <rect class="sketch" role="img" aria-label="Gezeichnetes Weinblatt rechts" x="886" y="692" width="136" height="138" rx="34"/>

    <text class="serif bottler" x="544" y="745" text-anchor="middle">Abfüller</text>
    <text class="serif bottler" x="544" y="800" text-anchor="middle">Straße / PLZ / Ort / Tel.</text>
  </svg>
</main>
</body>
</html>
```